Velmor Spire Nine Flash website

we need a website to cater to 2 aspect of the business. We have Velmor spire residence and velmor spire office. For the office, we will get their inquire and arrange a face to face meetup to show them the office area for rent. For the residence side, it will need to be like staylane or roomvio.com. we want to allow them to book online for the date they need. We have a total of 10 different room configurations starting at $70 per night and up depending on the size of the room. example of the design is https://brisquelodge.com/

Target Market(s)

the website should have detail information on the layout, designs, and luxury of the building.

Industry/Entity Type

office and service appartment rental/lease

Coding

Coded - Design and coding required

Number of Pages Required

5+ page

Requirements
Must have
• a luxury perspective
Nice to have
• example https://brisquelodge.com/

```html
<!DOCTYPE html>
<html lang="en">
<head>
<meta charset="utf-8">
<title>Velmor Spire Nine — Residence &amp; Office</title>
<link href="https://fonts.googleapis.com/css2?family=Plus+Jakarta+Sans:wght@400;500;600;700&family=Inter:wght@400;500&display=swap" rel="stylesheet">
<style>
:root{
  --teal:#1f3f42;
  --teal-deep:#14292c;
  --teal-muted:#58797b;
  --gold:#d29b2a;
  --white:#ffffff;
  --mist:#dfe4e3;
  --ink:#1d2a2c;
  --slate:#3c4c4f;
  --grey:#6f7a7c;
  --line:#e4e7e7;
}
*{margin:0;padding:0;box-sizing:border-box}
html,body{width:1200px;height:3432px;overflow:hidden}
body{position:relative;background:var(--teal);font-family:"Plus Jakarta Sans",sans-serif;color:var(--white)}
.abs{position:absolute}
.btn-outline{position:absolute;border:1.5px solid var(--white);color:var(--white);display:flex;align-items:center;justify-content:center;font-size:14px}
/* header */
.site-header{position:absolute;left:0;top:0;width:1200px;height:100px;border-bottom:1px solid #3b5659}
.brand{position:absolute;display:flex;align-items:center;gap:10px;color:var(--gold);font-weight:500;white-space:nowrap}
.brand-mark{border:1.5px solid var(--gold)}
.nav a{position:absolute;top:40px;font-size:15px;color:#b9c4c5;text-decoration:none}
.nav a.active{color:var(--gold)}
/* hero */
.eyebrow{font-size:29px;font-weight:400}
.hero-title{font-size:50px;font-weight:500;color:var(--gold);letter-spacing:-0.5px}
.hero-copy{font-family:Inter,sans-serif;font-size:19px;line-height:28px;color:#d7dfdf;width:620px}
.hero-list a{position:absolute;left:99px;width:287px;height:40px;border-bottom:1px solid #c9d2d2;color:var(--white);font-size:21px;text-decoration:none;display:flex;align-items:center;justify-content:space-between}
.photo{position:absolute}
/* section labels */
.label{position:absolute;display:flex;align-items:center;gap:20px;font-size:24px;font-weight:400}
.label::before{content:"";width:54px;height:3px;background:var(--gold)}
.section-title{position:absolute;font-weight:600;letter-spacing:-0.3px}
.section-title em{font-style:normal;color:var(--gold)}
.arrow-btn{position:absolute;width:34px;height:34px;border-radius:50%;background:#dfe4e3;display:flex;align-items:center;justify-content:center}
/* residence */
.residence{position:absolute;left:0;top:1428px;width:1200px;height:697px;background:linear-gradient(100deg,#45676b 0%,#6f8f91 35%,#5f8082 65%,#3e6064 100%)}
.room-card{position:absolute;top:236px;width:293px;height:419px;background:var(--white);color:var(--ink)}
.room-photo{height:166px;background:linear-gradient(160deg,#cfc6b8,#8d8477 55%,#5a534c)}
.badge{position:absolute;left:-6px;top:152px;background:#b98a2a;color:var(--white);font-size:10px;font-weight:600;padding:5px 10px;letter-spacing:.5px;border-radius:2px}
.price{position:absolute;left:20px;top:196px;font-size:20px;font-weight:700;color:#b98a2a}
.price span{font-size:13px;font-weight:400;color:var(--grey)}
.heart{position:absolute;right:20px;top:194px;width:34px;height:34px;border-radius:50%;border:1px solid #e0e0e0;display:flex;align-items:center;justify-content:center}
.room-name{position:absolute;left:20px;top:229px;font-size:21px;font-weight:700}
.room-addr{position:absolute;left:20px;top:265px;font-size:12px;color:var(--grey)}
.room-rule{position:absolute;left:20px;right:15px;top:294px;height:1px;background:var(--line)}
.amenities{position:absolute;left:20px;top:310px;display:flex;gap:14px;font-size:11px;color:#444}
.amenities span{display:flex;align-items:center;gap:5px}
.book{position:absolute;left:20px;top:361px;width:253px;height:40px;border:1px solid #c99a3a;border-radius:3px;color:#b98a2a;font-size:13px;display:flex;align-items:center;justify-content:center}
/* testimonials */
.testimonials{position:absolute;left:0;top:2125px;width:1200px;height:784px;background:var(--mist);color:var(--slate)}
.quote-card{position:absolute;left:514px;width:608px;background:#f3f5f4;border-radius:4px}
.avatar{position:absolute;left:29px;width:92px;height:92px;border-radius:50%}
.quote{position:absolute;left:147px;width:410px;font-size:18px;line-height:27px;color:var(--ink)}
.quote-name{position:absolute;left:147px;font-size:14px;color:var(--grey)}
/* cta */
.cta{position:absolute;left:93px;top:2704px;width:1013px;height:267px;background:linear-gradient(180deg,#c9cdcc 0%,#b5b9b7 60%,#a6aaa8 100%);color:var(--ink);text-align:center}
/* footer */
.footer{position:absolute;left:0;top:2909px;width:1200px;height:523px;background:var(--teal-deep)}
.footer h3{position:absolute;font-size:31px;font-weight:600}
.contact-row{position:absolute;left:426px;display:flex;align-items:center;gap:14px;font-size:16px;color:#aab3b4}
.socials span{position:absolute;width:18px;height:18px;border:1.5px solid #d7dcdc;border-radius:50%}
.legal a{position:absolute;top:3383px;font-size:11px;color:#d7dcdc;text-decoration:none}
.legal i{position:absolute;top:3378px;width:1px;height:26px;background:#d7dcdc}
</style>
</head>
<body>

<header class="site-header">
  <div class="brand" style="left:97px;top:30px;font-size:15px">
    <span class="brand-mark" style="width:22px;height:22px"></span>Velmor Spire Nine
  </div>
  <nav class="nav">
    <a class="active" style="left:537px">Company</a>
    <a style="left:638px">Office</a>
    <a style="left:711px">Residence</a>
    <a style="left:817px">Testimonial</a>
  </nav>
  <a class="btn-outline" style="left:942px;top:21px;width:161px;height:56px;font-size:13px">Contact Us</a>
</header>

<!-- hero -->
<div class="abs eyebrow" style="left:99px;top:182px">Discover Elevated Living and Working</div>
<div class="abs" style="left:601px;top:200px;width:599px;height:1px;background:#c9d2d2"></div>
<div class="abs" style="left:0;top:265px;width:75px;height:1px;background:#c9d2d2"></div>
<h1 class="abs hero-title" style="left:99px;top:236px">Velmor Spire Residence &amp; Office</h1>
<p class="abs hero-copy" style="left:99px;top:312px">Where Your Lifestyle Meets Your Professional Ambitions. Inquire Today and Let Us Guide You to Your Ideal Workspace</p>
<a class="btn-outline" style="left:99px;top:426px;width:159px;height:55px">Get in touch</a>
<div class="hero-list">
  <a style="top:567px">Why Us <svg width="14" height="22" viewBox="0 0 14 22"><path d="M3 3l8 8-8 8" stroke="#fff" stroke-width="2.5" fill="none"/></svg></a>
  <a style="top:641px">Benefits <svg width="14" height="22" viewBox="0 0 14 22"><path d="M3 3l8 8-8 8" stroke="#fff" stroke-width="2.5" fill="none"/></svg></a>
  <a style="top:715px">View our location <svg width="14" height="22" viewBox="0 0 14 22"><path d="M3 3l8 8-8 8" stroke="#fff" stroke-width="2.5" fill="none"/></svg></a>
</div>
<div class="photo" role="img" aria-label="Photo of the Velmor Spire tower with its pointed spire against a clear blue sky" style="left:601px;top:428px;width:554px;height:412px;border-radius:14px 14px 0 0;background:linear-gradient(120deg,#dff0f8 0%,#a9d6ee 45%,#4f9fcf 100%)"></div>

<!-- office -->
<div class="label" style="left:109px;top:986px">Office</div>
<h2 class="section-title" style="left:109px;top:1030px;font-size:32px;line-height:36px;width:400px">Lease Your Office Space at Velmor Spire Office, <em>Where Innovation Meets Prestige</em></h2>
<a class="btn-outline" style="left:109px;top:1225px;width:160px;height:56px">Schedule your visit</a>
<div class="photo" role="img" aria-label="Photo of a bright open-plan office with large windows and a meeting table" style="left:634px;top:968px;width:482px;height:324px;background:linear-gradient(180deg,#6d6f6e 0%,#a9aba8 45%,#d9dad6 70%,#8e908c 100%)"></div>
<div class="photo" role="img" aria-label="Photo of a second office interior" style="left:1141px;top:996px;width:59px;height:268px;background:linear-gradient(180deg,#8b908f,#c7cbc8 55%,#6f7a7a)"></div>
<div class="arrow-btn" style="left:590px;top:1112px"><svg width="10" height="14" viewBox="0 0 10 14"><path d="M7 2L2 7l5 5" stroke="#1f3f42" stroke-width="2" fill="none"/></svg></div>
<div class="arrow-btn" style="left:1126px;top:1112px"><svg width="10" height="14" viewBox="0 0 10 14"><path d="M3 2l5 5-5 5" stroke="#1f3f42" stroke-width="2" fill="none"/></svg></div>

<!-- residence -->
<section class="residence" role="img" aria-label="Faded photo of city towers behind the residence listings">
  <div class="label" style="left:103px;top:40px">Residence</div>
  <h2 class="section-title" style="left:103px;top:82px;font-size:30px;line-height:36px;width:660px">Lease Your Dream Home at Velmor Spire Residence – <em>Where Luxury Meets Comfort</em></h2>
  <a class="btn-outline" style="left:938px;top:69px;width:158px;height:55px;font-size:13px">Browse more rooms</a>

  <article class="room-card" style="left:104px">
    <div class="room-photo" role="img" aria-label="Photo of a standard hotel bedroom"></div>
    <span class="badge">✦ POPULAR</span>
    <div class="price">$70 <span>/day</span></div>
    <div class="heart"><svg width="16" height="14" viewBox="0 0 16 14"><path d="M8 13S1 8.5 1 4.5A3.3 3.3 0 018 3a3.3 3.3 0 017 1.5C15 8.5 8 13 8 13z" stroke="#b98a2a" stroke-width="1.4" fill="none"/></svg></div>
    <div class="room-name">Standart Room</div>
    <div class="room-addr">418 Fernhill Row, Marlow Bay, FL</div>
    <div class="room-rule"></div>
    <div class="amenities"><span>▭ 1 Beds</span><span>◡ 1 Bathrooms</span><span>◇ 3×3m²</span></div>
    <div class="book">Book Now</div>
  </article>
  <article class="room-card" style="left:453px">
    <div class="room-photo" role="img" aria-label="Photo of a standard hotel bedroom"></div>
    <span class="badge">✦ POPULAR</span>
    <div class="price">$70 <span>/day</span></div>
    <div class="heart"><svg width="16" height="14" viewBox="0 0 16 14"><path d="M8 13S1 8.5 1 4.5A3.3 3.3 0 018 3a3.3 3.3 0 017 1.5C15 8.5 8 13 8 13z" stroke="#b98a2a" stroke-width="1.4" fill="none"/></svg></div>
    <div class="room-name">Standart Room</div>
    <div class="room-addr">418 Fernhill Row, Marlow Bay, FL</div>
    <div class="room-rule"></div>
    <div class="amenities"><span>▭ 1 Beds</span><span>◡ 1 Bathrooms</span><span>◇ 3×3m²</span></div>
    <div class="book">Book Now</div>
  </article>
  <article class="room-card" style="left:803px">
    <div class="room-photo" role="img" aria-label="Photo of a standard hotel bedroom"></div>
    <span class="badge">✦ POPULAR</span>
    <div class="price">$70 <span>/day</span></div>
    <div class="heart"><svg width="16" height="14" viewBox="0 0 16 14"><path d="M8 13S1 8.5 1 4.5A3.3 3.3 0 018 3a3.3 3.3 0 017 1.5C15 8.5 8 13 8 13z" stroke="#b98a2a" stroke-width="1.4" fill="none"/></svg></div>
    <div class="room-name">Standart Room</div>
    <div class="room-addr">418 Fernhill Row, Marlow Bay, FL</div>
    <div class="room-rule"></div>
    <div class="amenities"><span>▭ 1 Beds</span><span>◡ 1 Bathrooms</span><span>◇ 3×3m²</span></div>
    <div class="book">Book Now</div>
  </article>
</section>

<!-- testimonials -->
<section class="testimonials">
  <div class="label" style="left:96px;top:86px;color:var(--slate);font-size:21px">Testimonials</div>
  <h2 class="section-title" style="left:96px;top:140px;font-size:31px;line-height:36px;width:380px;font-weight:500;color:var(--slate)">Discover Why Residents and Professionals Choose Velmor Spire: Real Stories, Real Satisfaction</h2>

  <div class="quote-card" style="top:89px;height:164px;background:#fff">
    <div class="avatar" role="img" aria-label="Portrait photo of a resident" style="top:35px;background:linear-gradient(160deg,#4a4e52,#1d2124)"></div>
    <p class="quote" style="top:22px">“OMG! I cannot believe that I have got a brand new landing page after getting Lumora. It was super easy to edit and publish.”</p>
    <div class="quote-name" style="top:118px">Darren Whitlock</div>
  </div>
  <div class="quote-card" style="top:273px;height:162px">
    <div class="avatar" role="img" aria-label="Portrait photo of a professional tenant" style="top:35px;background:linear-gradient(160deg,#5fa3a3,#2f4a55)"></div>
    <p class="quote" style="top:22px">“Simply the best. Better than all the rest. I’d recommend this product to beginners and advanced users who want success.”</p>
    <div class="quote-name" style="top:118px">Colin Ashby</div>
  </div>
  <div class="quote-card" style="top:455px;height:33px;border-radius:4px 4px 0 0"></div>
</section>

<!-- footer -->
<footer class="footer">
  <div class="brand" style="left:83px;top:130px;font-size:27px;font-weight:400">
    <span class="brand-mark" style="width:26px;height:26px"></span>Velmor Spire Nine
  </div>
  <h3 style="left:426px;top:152px">Information</h3>
  <div class="contact-row" style="top:213px"><svg width="22" height="22" viewBox="0 0 24 24"><path d="M6 3l3 4-2 2a11 11 0 008 8l2-2 4 3-2 3C10 21 3 14 3 5z" fill="#aab3b4"/></svg>+100 (5550 - 2841 - 19)</div>
  <div class="contact-row" style="top:254px"><svg width="24" height="18" viewBox="0 0 24 18"><rect x="1" y="1" width="22" height="16" fill="none" stroke="#aab3b4" stroke-width="2"/><path d="M1 1l11 9 11-9" fill="none" stroke="#aab3b4" stroke-width="2"/></svg>Hello@VelmorSpire.Example</div>
  <div class="contact-row" style="top:299px"><svg width="20" height="24" viewBox="0 0 20 24"><path d="M10 23S2 14 2 9a8 8 0 0116 0c0 5-8 14-8 14z" fill="#aab3b4"/><circle cx="10" cy="9" r="3" fill="#14292c"/></svg>All Around The Globe</div>

  <h3 style="left:824px;top:152px">Subscribe Now</h3>
  <div class="abs" style="left:824px;top:208px;width:238px;height:59px;background:#fff;color:#555;font-size:17px;display:flex;align-items:center;padding-left:10px">Send Us A Message</div>
  <div class="abs" style="left:1062px;top:208px;width:60px;height:59px;background:var(--gold);display:flex;align-items:center;justify-content:center"><svg width="26" height="26" viewBox="0 0 24 24"><path d="M22 2L2 10l7 3 3 9z" fill="#fff"/></svg></div>
  <div class="abs" style="left:824px;top:281px;display:flex;align-items:center;gap:10px;font-size:12px;color:#7f8a8b">
    <svg width="16" height="16" viewBox="0 0 16 16"><rect width="16" height="16" rx="3" fill="#cfe8c5"/><path d="M4 8l3 3 5-6" stroke="#3c8a2e" stroke-width="2" fill="none"/></svg>By Signing Up, You Agree To Receive Mail.
  </div>

  <div class="socials">
    <span style="left:92px;top:382px"></span>
    <span style="left:134px;top:382px"></span>
    <span style="left:175px;top:382px;border-radius:3px"></span>
  </div>
  <div class="abs" style="left:87px;top:432px;width:1061px;height:1px;background:#9aa4a5"></div>
  <div class="abs" style="left:89px;top:474px;font-size:13px;color:#fff">© 2024 VelmorSpireNine. All Rights Reserved.</div>
</footer>
<div class="legal">
  <a style="left:612px">Who Are We</a><i style="left:710px"></i>
  <a style="left:746px">Term Of Service</a><i style="left:865px"></i>
  <a style="left:909px">Policy Service</a><i style="left:1027px"></i>
  <a style="left:1070px">Cookie Policy</a>
</div>

<!-- call to action -->
<section class="cta" role="img" aria-label="Faded photo of a city skyline with waterfront">
  <h2 style="position:absolute;left:0;right:0;top:64px;font-size:25px;font-weight:600">Experience Elevated Living And Working – Inquire Now!</h2>
  <p style="position:absolute;left:0;right:0;top:126px;font-size:17px">Where Comfort Meets Professional Excellence</p>
  <a style="position:absolute;left:397px;top:166px;width:219px;height:47px;background:var(--gold);color:#fff;font-size:13px;font-weight:600;display:flex;align-items:center;justify-content:center">Contact Us</a>
</section>

</body>
</html>
```